Sophisticated, clean website reflecting my feminine, playful side to sell my abstract art,

I need a website no more than 3 pages to showcase my paintings, a little about me and some contact info. I do abstracts so looking for something a little edgy, yet feminine and current.
Updates

Hi there, These are some artists websites that I Iike: Marnelvoss.com (I like how airy it is) peterwallombry.com garethpolvens.com (I like how it scrolls) I'll need a place for a photo ( a headshot-i do not have it yet so I'll need to be able to upload that later) as well as an area for my bio. Also, it's important that I will be able to upload any new photos and descriptions easily so it should be user friendly. Lastly, I like in a sunny place so would like to have this seem upbeat and playful as that is how i like to paint. thanks-I'm trying to upload my photos now -

Target Market(s)

ppl ages 35-70 who want large scale art for their homes

Industry/Entity Type

art

Coding

Coded - Design and coding required

Number of Pages Required

3 page

Colors

Designer to choose colors to be used in the design.

Requirements
Must have
• photos of my art, a place for my bio, be easy to reach me. tasteful-nothing too "in your face" -my clients are pretty high end and organized. They like clean lines
Nice to have
• sophisticated background, muted tones in the back-similar clean font throughout-no cursive
Should not have
• too many dark areas. Too many blocks of color. Too serious.

```html
<!DOCTYPE html>
<html lang="en">
<head>
<meta charset="utf-8">
<title>Marla Quen Art – Homepage Concepts</title>
<link href="https://fonts.googleapis.com/css2?family=Playfair+Display:wght@500;700&family=Lato:wght@400;700&family=Great+Vibes&display=swap" rel="stylesheet">
<style>
:root{
  --stage:#8a8a8a;
  --salmon:#efa898;
  --band:#eaa696;
  --peach:#f6c8ae;
  --ink:#1d1d1d;
  --muted:#666;
  --paper:#ffffff;
  --soft:#f5f5f5;
  --night:#000000;
}
*{box-sizing:border-box;margin:0;padding:0}
html,body{width:853px;height:1200px;overflow:hidden;background:var(--stage)}
body{position:relative;font-family:'Lato',sans-serif;color:var(--ink)}
.defs{position:absolute;width:0;height:0}
.page{position:absolute;width:405px;background:var(--paper);overflow:hidden;box-shadow:0 2px 6px rgba(0,0,0,.25)}
.page--a{left:10px;top:10px;height:958px}
.page--b{left:430px;top:10px;height:1166px}
.abs{position:absolute}
.topline{left:0;top:0;width:100%;height:2px;background:var(--salmon)}
.brand{font-family:'Playfair Display',serif;font-weight:700;color:var(--salmon);line-height:.95;text-transform:uppercase}
.brand--head{left:45px;top:7px;font-size:7.5px}
.nav{top:11px;left:167px;display:flex;gap:9px;font-size:4.4px;font-weight:700;text-transform:uppercase}
.nav .active{color:var(--salmon);font-weight:400}
.socials{display:flex;gap:5px}
.socials span{width:10px;height:10px;border:.8px solid var(--salmon);border-radius:50%;display:flex;align-items:center;justify-content:center}
.socials svg{width:5px;height:5px;fill:var(--salmon)}
.socials--head{left:304px;top:9px}
.hero-photo{left:45px;top:30px;width:158px;height:189px;background:linear-gradient(90deg,#9a6a3c,#c08a55 8%,#b07a48 92%,#8e6034)}
.hero-photo i{position:absolute;left:22px;top:18px;width:106px;height:150px;background:linear-gradient(180deg,#e8e4dc 0 30%,#4a8fb8 34%,#a9cde0 55%,#dfe6ea)}
.hero-panel{left:203px;top:30px;width:158px;height:189px;background:var(--salmon);text-align:center;color:#fff}
.script{font-family:'Great Vibes',cursive;font-size:22px;margin-top:34px;line-height:1}
.hero-title{font-family:'Playfair Display',serif;font-weight:700;font-size:20px;line-height:1.05;margin-top:4px;text-transform:uppercase}
.hero-text{font-size:4.2px;line-height:2;margin:6px 10px 0}
.btn{display:inline-block;background:var(--peach);color:#fff;font-family:'Playfair Display',serif;font-weight:700;font-size:5px;text-transform:uppercase;border-radius:0 8px 0 8px;text-align:center}
.btn--hero{width:64px;height:16px;line-height:16px;margin-top:6px}
.accent{background:radial-gradient(circle,rgba(239,168,152,.22),rgba(239,168,152,0) 70%)}
.sec-title{left:0;width:100%;text-align:center;font-family:'Playfair Display',serif;font-weight:700;font-size:10.5px;color:var(--salmon);text-transform:uppercase}
.sec-sub{left:0;width:100%;text-align:center;font-size:4.4px}
.arrow{width:16px;height:16px;border-radius:50%;background:var(--salmon);color:#fff;font-size:8px;line-height:15px;text-align:center;font-weight:700}
.frame{background:#fff;box-shadow:0 1px 4px rgba(0,0,0,.2);padding:2px}
.frame--active{background:var(--salmon)}
.frame > div{width:100%;height:100%}
.cap{text-align:center;width:80px}
.cap b{display:block;font-family:'Playfair Display',serif;font-size:5px;text-transform:uppercase;margin-bottom:2px}
.cap p{font-size:3.9px;line-height:2}
.card{background:#fff;border:.6px solid #ddd;border-radius:4px;overflow:hidden;text-align:center}
.card--lift{box-shadow:0 2px 6px rgba(0,0,0,.2)}
.card .img{height:75px;position:relative}
.heart{position:absolute;right:4px;top:5px;background:#fff;border-radius:4px;font-size:3.6px;font-weight:700;padding:1px 3px}
.heart::before{content:"";display:inline-block;width:3px;height:3px;background:#e23;border-radius:50%;margin-right:1px}
.card small{display:block;font-size:3px;color:var(--salmon);margin-top:6px}
.card b{display:block;font-family:'Playfair Display',serif;font-size:6px;margin-top:2px}
.card p{font-size:3.8px;color:var(--muted);line-height:2;margin:2px 8px 0}
.band{left:0;top:447px;width:100%;height:193px;background:linear-gradient(120deg,#eeab9b,#e59a89)}
.band-text{left:229px;top:490px;width:149px;color:#fff;text-align:center}
.band-text h2{font-family:'Playfair Display',serif;font-weight:500;font-size:11px;text-transform:uppercase}
.band-text .lead{font-size:4.2px;margin-top:4px}
.band-text .body{font-size:4.2px;line-height:2.2;text-align:justify;margin-top:8px}
.btn--band{width:64px;height:16px;line-height:16px;margin-top:5px;background:#f4c7ae}
.ico{width:20px;height:20px;border-radius:50%;background:var(--salmon);display:flex;align-items:center;justify-content:center}
.info b{display:block;font-family:'Playfair Display',serif;font-weight:500;font-size:5.2px;text-transform:uppercase}
.info p{font-size:5px;line-height:1.7;margin-top:1px}
.form-title{font-family:'Playfair Display',serif;font-weight:500;font-size:5.2px;text-transform:uppercase}
.field{border-bottom:.6px solid #555;font-size:3.8px;padding-left:3px}
.btn--submit{width:63px;height:16px;line-height:16px;background:var(--salmon);color:#fff}
.footer{left:0;width:100%;background:var(--night);color:#fff;text-align:center}
.footer .brand{font-size:10px}
.fnav{display:flex;justify-content:center;gap:11px;font-size:5.4px;font-weight:700;text-transform:uppercase}
.copy{font-size:3.5px}
</style>
</head>
<body>

<svg class="defs" aria-hidden="true">
  <symbol id="i-heart" viewBox="0 0 10 10"><path d="M5 9L1 5a2.3 2.3 0 0 1 4-3 2.3 2.3 0 0 1 4 3z"/></symbol>
  <symbol id="i-mail" viewBox="0 0 10 10"><path d="M0 2h10v6H0zM.6 2.6L5 5.6l4.4-3" /></symbol>
  <symbol id="i-star" viewBox="0 0 10 10"><path d="M5 0l1.5 3.4 3.5.3-2.7 2.3.9 3.5L5 7.6 1.8 9.5l.9-3.5L0 3.7l3.5-.3z"/></symbol>
  <symbol id="i-share" viewBox="0 0 10 10"><circle cx="2" cy="5" r="1.6"/><circle cx="8" cy="2" r="1.6"/><circle cx="8" cy="8" r="1.6"/><path d="M2 5l6-3M2 5l6 3" stroke="currentColor" stroke-width=".8"/></symbol>
</svg>

<!-- Concept A -->
<section class="page page--a">
  <div class="abs topline"></div>
  <div class="abs brand brand--head">Marla<br>Quen Art</div>
  <nav class="abs nav"><span class="active">Home</span><span>My Paintings</span><span>About Me</span><span>Contact Me</span></nav>
  <div class="abs socials socials--head"><span><svg><use href="#i-heart"/></svg></span><span><svg><use href="#i-mail"/></svg></span><span><svg><use href="#i-star"/></svg></span><span><svg><use href="#i-share"/></svg></span></div>

  <div class="abs accent" role="img" aria-label="Soft brush-stroke accent" style="left:19px;top:36px;width:50px;height:50px"></div>
  <div class="abs hero-photo" role="img" aria-label="Blue drip abstract painting leaning on a wooden wall"><i></i></div>
  <div class="abs hero-panel">
    <div class="script">Welcome to</div>
    <div class="hero-title">Marla<br>Quen Art</div>
    <p class="hero-text">Lorem ipsum dolor sit amet, consectetur adipiscing elit, sed do eiusmod tempor incididunt ut labore et dolore magna aliqua Quis ipsum suspendisse ultrices gravida.</p>
    <span class="btn btn--hero">Get Started</span>
  </div>
  <div class="abs accent" role="img" aria-label="Soft brush-stroke accent" style="left:330px;top:175px;width:58px;height:58px"></div>

  <h2 class="abs sec-title" style="top:254px">My Paintings</h2>
  <p class="abs sec-sub" style="top:273px">Lorem ipsum dolor sit amet consectetur adipiscing elit</p>
  <div class="abs arrow" style="left:24px;top:327px">‹</div>
  <div class="abs arrow" style="left:366px;top:327px">›</div>
  <div class="abs frame" style="left:45px;top:291px;width:74px;height:87px"><div role="img" aria-label="Swirling gold and blue abstract painting" style="background:linear-gradient(135deg,#d9a23a,#e8e4d6 40%,#3b5fa8 70%,#d8b34a)"></div></div>
  <div class="abs frame frame--active" style="left:125px;top:291px;width:75px;height:87px"><div role="img" aria-label="Green and black floral abstract painting" style="background:linear-gradient(135deg,#3f9a4a,#1e2a24 45%,#6cbf6a 75%,#e6e3da)"></div></div>
  <div class="abs frame" style="left:206px;top:291px;width:74px;height:87px"><div role="img" aria-label="Purple floral abstract painting" style="background:linear-gradient(135deg,#7a5c8f,#d8cfd6 40%,#4a3a6e 70%,#b9a3c4)"></div></div>
  <div class="abs frame" style="left:286px;top:291px;width:74px;height:87px"><div role="img" aria-label="Burgundy rose abstract painting" style="background:linear-gradient(135deg,#e6ddd8,#6b2a2a 40%,#c99a90 70%,#efe7e3)"></div></div>
  <div class="abs cap" style="left:42px;top:387px"><b>Lorem ipsum dolor</b><p>Lorem ipsum dolor sit amet, consectetur adipiscing elit, sed do eiusmod tempor.</p></div>
  <div class="abs cap" style="left:122px;top:387px"><b>Lorem ipsum dolor</b><p>Lorem ipsum dolor sit amet, consectetur adipiscing elit, sed do eiusmod tempor.</p></div>
  <div class="abs cap" style="left:203px;top:387px"><b>Lorem ipsum dolor</b><p>Lorem ipsum dolor sit amet, consectetur adipiscing elit, sed do eiusmod tempor.</p></div>
  <div class="abs cap" style="left:283px;top:387px"><b>Lorem ipsum dolor</b><p>Lorem ipsum dolor sit amet, consectetur adipiscing elit, sed do eiusmod tempor.</p></div>

  <div class="abs band"></div>
  <div class="abs frame" style="left:28px;top:488px;width:95px;height:113px"><div role="img" aria-label="Yellow and blue abstract painting" style="background:linear-gradient(140deg,#e8e6e0,#e3c53a 35%,#4f76c4 60%,#e9e7e2)"></div></div>
  <div class="abs frame" style="left:97px;top:474px;width:117px;height:139px"><div role="img" aria-label="Portrait of the artist seated with a paintbrush in her studio" style="background:linear-gradient(90deg,#d9d6d0,#cfc8bf 40%,#4c4a3a 70%,#3f5a78)"></div></div>
  <div class="abs band-text">
    <h2>About Me</h2>
    <p class="lead">Lorem ipsum dolor sit amet consectetur adipiscing elit</p>
    <p class="body">Lorem ipsum dolor sit amet, consectetur adipiscing elit, sed do eiusmod tempor incididunt ut labore et dolore magna aliqua. Quis ipsum suspendisse ultrices gravida. Risus commodo viverra maecenas accumsan lacus vel facilisis. Lorem ipsum dolor sit amet, consectetur adipiscing elit, sed do eiusmod tempor incididunt ut labore et dolore magna aliqua. Ut enim ad minim veniam, quis nostrud exercitation ullamco laboris nisi ut aliquip ex ea commodo consequat.</p>
    <span class="btn btn--band">Learn More</span>
  </div>

  <h2 class="abs sec-title" style="top:670px">Contact Us</h2>
  <p class="abs sec-sub" style="top:688px">Lorem ipsum dolor sit amet consectetur adipiscing elit</p>
  <div class="abs ico" style="left:45px;top:720px"><svg width="8" height="9" viewBox="0 0 8 10"><path d="M4 0a3.5 3.5 0 0 0-3.5 3.5C.5 6 4 10 4 10s3.5-4 3.5-6.5A3.5 3.5 0 0 0 4 0z" fill="#fff"/><circle cx="4" cy="3.5" r="1.2" fill="#efa898"/></svg></div>
  <div class="abs info" style="left:71px;top:722px;width:100px"><b>Location</b><p>123 Lorem ipsum dolor sit amet conse ctetur adipiscing elit.</p></div>
  <div class="abs ico" style="left:45px;top:759px"><svg width="8" height="8" viewBox="0 0 10 10"><path d="M2 0l2 2.5-1.2 1.3a6 6 0 0 0 3.4 3.4L7.5 6 10 8l-1.5 2C4 10 0 6 0 1.5z" fill="#fff"/></svg></div>
  <div class="abs info" style="left:71px;top:764px"><b>Phone Number</b><p>+1 888 888 8888</p></div>
  <div class="abs ico" style="left:45px;top:795px"><svg width="8" height="6" viewBox="0 0 10 7"><rect width="10" height="7" rx="1" fill="#fff"/><path d="M0 .5l5 3.5 5-3.5" stroke="#efa898" fill="none" stroke-width=".8"/></svg></div>
  <div class="abs info" style="left:71px;top:800px"><b>Email Address</b><p>hello@marlaquenart.com</p></div>
  <div class="abs form-title" style="left:194px;top:713px">Send Us A Message</div>
  <div class="abs field" style="left:195px;top:734px;width:80px;height:10px">Your Name</div>
  <div class="abs field" style="left:281px;top:734px;width:80px;height:10px">Email</div>
  <div class="abs field" style="left:195px;top:755px;width:80px;height:10px">Phone Number</div>
  <div class="abs field" style="left:281px;top:755px;width:80px;height:10px">Subject</div>
  <div class="abs field" style="left:195px;top:776px;width:166px;height:16px">Message</div>
  <span class="abs btn btn--submit" style="left:195px;top:805px">Submit</span>

  <footer class="abs footer" style="top:843px;height:115px">
    <div class="brand" style="margin-top:24px">Marla<br>Quen Art</div>
    <div class="fnav" style="margin-top:12px"><span>Home</span><span>My Paintings</span><span>About Me</span><span>Contact Me</span></div>
    <div class="socials" style="justify-content:center;margin-top:8px"><span><svg><use href="#i-heart"/></svg></span><span><svg><use href="#i-mail"/></svg></span><span><svg><use href="#i-star"/></svg></span><span><svg><use href="#i-share"/></svg></span></div>
    <p class="copy" style="margin-top:6px">© copyrights 2022 Marla Quen Art &nbsp;| &nbsp;&nbsp;All rights reserved.</p>
  </footer>
</section>

<!-- Concept B -->
<section class="page page--b">
  <div class="abs topline"></div>
  <div class="abs brand brand--head">Marla<br>Quen Art</div>
  <nav class="abs nav"><span class="active">Home</span><span>My Paintings</span><span>About Me</span><span>Contact Me</span></nav>
  <div class="abs socials socials--head"><span><svg><use href="#i-heart"/></svg></span><span><svg><use href="#i-mail"/></svg></span><span><svg><use href="#i-star"/></svg></span><span><svg><use href="#i-share"/></svg></span></div>

  <div class="abs accent" role="img" aria-label="Soft brush-stroke accent" style="left:19px;top:36px;width:50px;height:50px"></div>
  <div class="abs hero-photo" role="img" aria-label="Blue drip abstract painting leaning on a wooden wall"><i></i></div>
  <div class="abs hero-panel">
    <div class="script">Welcome to</div>
    <div class="hero-title">Marla<br>Quen Art</div>
    <p class="hero-text">Lorem ipsum dolor sit amet, consectetur adipiscing elit, sed do eiusmod tempor incididunt ut labore et dolore magna aliqua Quis ipsum suspendisse ultrices gravida.</p>
    <span class="btn btn--hero">Get Started</span>
  </div>
  <div class="abs accent" role="img" aria-label="Soft brush-stroke accent" style="left:330px;top:175px;width:58px;height:58px"></div>

  <h2 class="abs sec-title" style="top:254px">My Paintings</h2>
  <p class="abs sec-sub" style="top:273px">Lorem ipsum dolor sit amet consectetur adipiscing elit</p>
  <div class="abs arrow" style="left:24px;top:327px">‹</div>
  <div class="abs arrow" style="left:366px;top:327px">›</div>
  <div class="abs card" style="left:49px;top:289px;width:93px;height:119px">
    <div class="img" role="img" aria-label="Teal abstract painting on wood" style="background:linear-gradient(90deg,#5a6a8a,#e8e2d6 25%,#0f8f80 35%,#0f8f80 70%,#e8e2d6 78%,#1f2a4a)"><span class="heart">12</span></div>
    <small>Blanditiis</small><b>Marla Quen Art</b><p>Nam libero tempore, cum soluta nobis est eligendi optio cumque.</p>
  </div>
  <div class="abs card card--lift" style="left:156px;top:289px;width:93px;height:119px">
    <div class="img" role="img" aria-label="Green and black floral abstract painting" style="background:linear-gradient(135deg,#3f9a4a,#1e2a24 45%,#6cbf6a 75%,#e6e3da)"><span class="heart">74</span></div>
    <small>Lorem Ipsum</small><b>Marla Quen Art</b><p>Itaque earum rerum hic tenetur a sapiente delectus, ut aut reiciendis</p>
  </div>
  <div class="abs card" style="left:263px;top:289px;width:93px;height:119px">
    <div class="img" role="img" aria-label="Blue drip abstract painting on wood" style="background:linear-gradient(180deg,#b08250,#e8e4dc 20%,#4a8fb8 40%,#dfe6ea 80%,#b08250)"><span class="heart">31</span></div>
    <small>Voluptem Sans</small><b>Marla Quen Art</b><p>Nam libero tempore, cum soluta nobis est eligendi optio cumque.</p>
  </div>

  <div class="abs band"></div>
  <div class="abs frame" style="left:28px;top:488px;width:95px;height:113px"><div role="img" aria-label="Yellow and blue abstract painting" style="background:linear-gradient(140deg,#e8e6e0,#e3c53a 35%,#4f76c4 60%,#e9e7e2)"></div></div>
  <div class="abs frame" style="left:97px;top:474px;width:117px;height:139px"><div role="img" aria-label="Portrait of the artist seated with a paintbrush in her studio" style="background:linear-gradient(90deg,#d9d6d0,#cfc8bf 40%,#4c4a3a 70%,#3f5a78)"></div></div>
  <div class="abs band-text">
    <h2>About Me</h2>
    <p class="lead">Lorem ipsum dolor sit amet consectetur adipiscing elit</p>
    <p class="body">Lorem ipsum dolor sit amet, consectetur adipiscing elit, sed do eiusmod tempor incididunt ut labore et dolore magna aliqua. Quis ipsum suspendisse ultrices gravida. Risus commodo viverra maecenas accumsan lacus vel facilisis. Lorem ipsum dolor sit amet, consectetur adipiscing elit, sed do eiusmod tempor incididunt ut labore et dolore magna aliqua. Ut enim ad minim veniam, quis nostrud exercitation ullamco laboris nisi ut aliquip ex ea commodo consequat.</p>
    <span class="btn btn--band">Learn More</span>
  </div>

  <h2 class="abs sec-title" style="top:678px">Our Gallery</h2>
  <p class="abs sec-sub" style="top:697px">Lorem ipsum dolor sit amet consectetur adipiscing elit</p>
  <div class="abs" role="img" aria-label="Blue drip painting" style="left:0;top:717px;width:48px;height:89px;background:linear-gradient(180deg,#e8e4dc 20%,#4a8fb8 40%,#dfe6ea 85%,#b08250)"></div>
  <div class="abs" role="img" aria-label="Green floral painting" style="left:54px;top:732px;width:45px;height:58px;background:linear-gradient(135deg,#3f9a4a,#1e2a24 45%,#6cbf6a)"></div>
  <div class="abs" role="img" aria-label="Purple floral painting" style="left:104px;top:717px;width:70px;height:89px;background:linear-gradient(135deg,#7a5c8f,#d8cfd6 40%,#4a3a6e 70%,#b9a3c4)"></div>
  <div class="abs" role="img" aria-label="Gold and blue swirl painting" style="left:180px;top:732px;width:45px;height:58px;background:linear-gradient(135deg,#d9a23a,#e8e4d6 40%,#3b5fa8 70%,#d8b34a)"></div>
  <div class="abs" role="img" aria-label="Teal abstract painting, highlighted" style="left:230px;top:717px;width:70px;height:89px;border:1px solid #e64f9a;background:linear-gradient(90deg,#e8e2d6 12%,#0f8f80 22%,#0f8f80 80%,#e8e2d6 90%)"></div>
  <div class="abs" style="left:261px;top:713px;width:8px;height:8px;border-radius:2px;background:#e64f9a"></div>
  <div class="abs" role="img" aria-label="Burgundy rose painting" style="left:306px;top:732px;width:45px;height:58px;background:linear-gradient(135deg,#e6ddd8,#6b2a2a 40%,#c99a90 70%)"></div>
  <div class="abs" role="img" aria-label="Yellow and blue abstract painting" style="left:357px;top:717px;width:48px;height:89px;background:linear-gradient(140deg,#e8e6e0,#4f76c4 35%,#e3c53a 60%,#e9e7e2)"></div>

  <div class="abs" style="left:0;top:849px;width:100%;height:200px;background:var(--soft)"></div>
  <h2 class="abs sec-title" style="top:876px">Contact Us</h2>
  <p class="abs sec-sub" style="top:894px">Lorem ipsum dolor sit amet consectetur adipiscing elit</p>
  <div class="abs ico" style="left:45px;top:926px"><svg width="8" height="9" viewBox="0 0 8 10"><path d="M4 0a3.5 3.5 0 0 0-3.5 3.5C.5 6 4 10 4 10s3.5-4 3.5-6.5A3.5 3.5 0 0 0 4 0z" fill="#fff"/><circle cx="4" cy="3.5" r="1.2" fill="#efa898"/></svg></div>
  <div class="abs info" style="left:71px;top:928px;width:100px"><b>Location</b><p>123 Lorem ipsum dolor sit amet conse ctetur adipiscing elit.</p></div>
  <div class="abs ico" style="left:45px;top:964px"><svg width="8" height="8" viewBox="0 0 10 10"><path d="M2 0l2 2.5-1.2 1.3a6 6 0 0 0 3.4 3.4L7.5 6 10 8l-1.5 2C4 10 0 6 0 1.5z" fill="#fff"/></svg></div>
  <div class="abs info" style="left:71px;top:969px"><b>Phone Number</b><p>+1 888 888 8888</p></div>
  <div class="abs ico" style="left:45px;top:1001px"><svg width="8" height="6" viewBox="0 0 10 7"><rect width="10" height="7" rx="1" fill="#fff"/><path d="M0 .5l5 3.5 5-3.5" stroke="#efa898" fill="none" stroke-width=".8"/></svg></div>
  <div class="abs info" style="left:71px;top:1006px"><b>Email Address</b><p>hello@marlaquenart.com</p></div>
  <div class="abs form-title" style="left:194px;top:919px">Send Us A Message</div>
  <div class="abs field" style="left:195px;top:940px;width:80px;height:10px">Your Name</div>
  <div class="abs field" style="left:281px;top:940px;width:80px;height:10px">Email</div>
  <div class="abs field" style="left:195px;top:961px;width:80px;height:10px">Phone Number</div>
  <div class="abs field" style="left:281px;top:961px;width:80px;height:10px">Subject</div>
  <div class="abs field" style="left:195px;top:982px;width:166px;height:16px">Message</div>
  <span class="abs btn btn--submit" style="left:195px;top:1010px">Submit</span>

  <footer class="abs footer" style="top:1049px;height:117px">
    <div class="brand" style="margin-top:24px">Marla<br>Quen Art</div>
    <div class="fnav" style="margin-top:12px"><span>Home</span><span>My Paintings</span><span>About Me</span><span>Contact Me</span></div>
    <div class="socials" style="justify-content:center;margin-top:8px"><span><svg><use href="#i-heart"/></svg></span><span><svg><use href="#i-mail"/></svg></span><span><svg><use href="#i-star"/></svg></span><span><svg><use href="#i-share"/></svg></span></div>
    <p class="copy" style="margin-top:6px">© copyrights 2022 Marla Quen Art &nbsp;| &nbsp;&nbsp;All rights reserved.</p>
  </footer>
</section>

</body>
</html>
```